Web Developer Needs a Business Card Design

I need a personal business card design that represents me as a web developer for potential employers. I would like the background to be a dark color on the front for contrast with my logo and name. The back will have all my information along with a smaller version of the logo. I want something with a modern look and feel, not too conservative. This will be used for potential employers and freelance work.

Industry/Entity Type

Business

Contact Information for Business Card

Front should have my logo and name. The back should have all my personal information which would include: name: Tom Varulek, phone: 570-614-3098, email: tomvarulek@quillbox.net, website url: www.tomvarulek.net, logo, web developer.

Font styles to use
Sans Serif

Requirements
Must have
• Must include my logo. The color palette base color will be the logo color.

```html
<!DOCTYPE html>
<html lang="en">
<head>
<meta charset="utf-8">
<title>Tom Varulek — Business Card</title>
<link href="https://fonts.googleapis.com/css2?family=Questrial&display=swap" rel="stylesheet">
<style>
  :root {
    --backdrop: #8b8c8b;
    --ink-dark: #231f1e;
    --teal: #4ecbad;
    --paper: #ebebeb;
    --text: #2b2b2b;
  }
  * { margin: 0; padding: 0; box-sizing: border-box; }
  html, body {
    width: 1200px;
    height: 900px;
    overflow: hidden;
    background: var(--backdrop);
    font-family: "Questrial", sans-serif;
  }
  .card {
    position: absolute;
    left: 346px;
    width: 508px;
    height: 290px;
    overflow: hidden;
  }
  .card--front { top: 119px; background: var(--ink-dark); }
  .card--back { top: 470px; background: var(--paper); }

  .pattern-fill {
    position: absolute;
    inset: 0;
    background: radial-gradient(circle at 50% 50%, #2c2b28 0%, #242120 70%, #201d1c 100%);
  }
  .wordmark {
    position: absolute;
    display: flex;
    align-items: center;
    gap: 10px;
    color: var(--teal);
    white-space: nowrap;
  }
  .wordmark__dot {
    width: 14px;
    height: 14px;
    border-radius: 50%;
    background: var(--teal);
    flex: none;
  }
  .card--front .wordmark {
    left: 50%;
    top: 50%;
    transform: translate(-50%, -50%);
    font-size: 34px;
  }
  .card--back .wordmark {
    left: 50%;
    top: 58px;
    transform: translateX(-50%);
    font-size: 30px;
  }

  .identity {
    position: absolute;
    left: 0;
    right: 0;
    top: 128px;
    text-align: center;
  }
  .identity__name {
    color: var(--teal);
    font-size: 24px;
    line-height: 26px;
    letter-spacing: 0.5px;
  }
  .identity__role {
    color: var(--text);
    font-size: 15px;
    line-height: 18px;
  }

  .contact-band {
    position: absolute;
    left: 0;
    right: 0;
    bottom: 0;
    height: 102px;
    background: var(--teal);
    padding: 17px 30px 0 30px;
    display: flex;
    justify-content: space-between;
    color: var(--text);
    font-size: 14px;
  }
  .contact-list { list-style: none; }
  .contact-list li {
    height: 22px;
    display: flex;
    align-items: center;
    gap: 8px;
  }
  .contact-list--links li { justify-content: flex-end; }
  .contact-icon { width: 13px; height: 13px; fill: var(--text); flex: none; }
  .link-marker {
    width: 12px;
    height: 12px;
    border-radius: 50%;
    background: var(--text);
    flex: none;
  }
</style>
</head>
<body>

<section class="card card--front">
  <div class="pattern-fill" role="img" aria-label="Faint repeating monogram pattern in dark green-grey"></div>
  <div class="wordmark"><span class="wordmark__dot"></span><span>Varulek</span></div>
</section>

<section class="card card--back">
  <div class="wordmark"><span class="wordmark__dot"></span><span>Varulek</span></div>

  <div class="identity">
    <p class="identity__name">Tom Varulek</p>
    <p class="identity__role">Front-End Developer</p>
  </div>

  <div class="contact-band">
    <ul class="contact-list">
      <li>
        <svg class="contact-icon" viewBox="0 0 16 16" aria-hidden="true"><path d="M3.5 1 6 1.4 7 4.6 5.4 6a9 9 0 0 0 4.6 4.6L11.4 9l3.2 1 .4 2.5-1.6 1.8C7.5 14.5 1.5 8.5 1.7 2.6z"/></svg>
        <span>570-614-3098</span>
      </li>
      <li>
        <svg class="contact-icon" viewBox="0 0 16 16" aria-hidden="true"><path d="M1 3.5h14v9H1z M1.8 4.2 8 9l6.2-4.8" fill="none" stroke="#2b2b2b" stroke-width="1.4"/><path d="M1 4l7 5 7-5v8.5H1z"/></svg>
        <span>tomvarulek@quillbox.net</span>
      </li>
      <li>
        <svg class="contact-icon" viewBox="0 0 16 16" aria-hidden="true"><circle cx="8" cy="8" r="6.6" fill="none" stroke="#2b2b2b" stroke-width="1.6"/><ellipse cx="8" cy="8" rx="2.6" ry="6.6" fill="none" stroke="#2b2b2b" stroke-width="1.2"/><path d="M1.5 8h13" stroke="#2b2b2b" stroke-width="1.2"/></svg>
        <span>www.tomvarulek.net</span>
      </li>
    </ul>
    <ul class="contact-list contact-list--links">
      <li><span>@tomvarulek.net</span><span class="link-marker"></span></li>
      <li><span>tomvarulek.net</span><span class="link-marker"></span></li>
      <li><span>tomvarulek.net</span><span class="link-marker"></span></li>
    </ul>
  </div>
</section>

</body>
</html>
```